Buch-/eBook-Cover für Anti-Stress-Adventskalender
TR Verlagshaus suchte ein neues Design in der Kategorie Buch-/eBook-Cover und hat ein Projekt auf grafikwerkstatt-online.de gestartet.
Zielgruppe
Wir sind als Selfpublisher vorwiegend bei Larvo Druckdienst aktiv und veröffentlichen Taschenbücher im Bereich Sachbücher, Ratgeber und Kinderbücher. Die Zielgruppe ist bei diesem Projekt schwieriger zu bestimmten, aber wird vsl. im Bereich der jungen Erwachsenen liegen und tendenziell eher im weiblichen Publikum.
Aufgabenstellung
Das Design sollte ein individuell auf das Projekt und auf die Zielgruppe abgestimmtes Konzept verfolgen, welches auf Larvo in die Augen sticht und Besteller Potential hat. Es sollte sich an bereits vorhanden Bestsellern in der jeweiligen Nische orientieren und dabei trotzdem die eigene Idee verdeutlichen. Der Sarkasmus und Humor des Buches und des Haupttitels sollte aus dem Cover hervorgehen.
Der Haupttitel: 17 Gründe, den Osterhasen trotzdem zu mögen
Der Nebentitel: Dein heiterer Entspannungs-Wochenplaner mit schrägen Geschichten, Knobeleien und bunten Übungen.
Autor: Jonas Riedl
Die Maße des Taschenbuchs werden wie folgt sein: 15.24 x 0.64 x 22.86 cm

```html
<!DOCTYPE html>
<html lang="de">
<head>
<meta charset="utf-8">
<title>17 Gründe, den Osterhasen trotzdem zu mögen – Cover</title>
<link rel="stylesheet" href="https://fonts.googleapis.com/css2?family=Mali:wght@700&family=Patrick+Hand+SC&family=Gochi+Hand&display=swap">
<style>
  :root {
    --stage: #4a1a19;
    --cover-yellow: #fce375;
    --ink-navy: #253344;
    --title-red: #e84a42;
    --title-shadow: #b3a96a;
    --badge-red: #e8534a;
    --outline: #1d1d1d;
    --white: #ffffff;
    --art-red: #d9463d;
    --art-cream: #f4ece0;
  }
  html, body {
    margin: 0;
    padding: 0;
    width: 1200px;
    height: 1200px;
    overflow: hidden;
    background: var(--stage);
  }
  .cover {
    position: absolute;
    left: 180px;
    top: 30px;
    width: 840px;
    height: 1140px;
    background: var(--cover-yellow);
    overflow: hidden;
  }
  .title-main {
    position: absolute;
    top: 44px;
    left: 0;
    width: 100%;
    margin: 0;
    text-align: center;
    white-space: nowrap;
    font-family: "Mali", sans-serif;
    font-weight: 700;
    font-size: 112px;
    line-height: 1.2;
    color: var(--ink-navy);
    text-shadow: 9px 9px 0 var(--title-shadow);
  }
  .title-sub {
    position: absolute;
    top: 236px;
    left: 0;
    width: 100%;
    margin: 0;
    text-align: center;
    font-family: "Mali", sans-serif;
    font-weight: 700;
    font-size: 56px;
    line-height: 1.15;
    color: var(--title-red);
    -webkit-text-stroke: 2px var(--outline);
    paint-order: stroke fill;
  }
  .divider {
    position: absolute;
    top: 398px;
    left: 276px;
    width: 314px;
    height: 4px;
    background: var(--ink-navy);
    border-radius: 2px;
  }
  .tagline {
    position: absolute;
    top: 418px;
    left: 0;
    width: 100%;
    margin: 0;
    text-align: center;
    font-family: "Patrick Hand SC", sans-serif;
    font-size: 30px;
    color: var(--ink-navy);
    letter-spacing: 0.5px;
  }
  .illustration {
    position: absolute;
    left: 97px;
    top: 553px;
    width: 520px;
    height: 587px;
  }
  .badge {
    position: absolute;
    left: 464px;
    top: 480px;
    width: 314px;
    height: 314px;
    border-radius: 50%;
    background: var(--badge-red);
    border: 4px solid var(--outline);
    box-sizing: border-box;
    display: flex;
    align-items: center;
    justify-content: center;
    text-align: center;
    padding: 0 40px;
    font-family: "Gochi Hand", cursive;
    font-size: 26px;
    line-height: 1.2;
    letter-spacing: 1px;
    color: var(--white);
    text-transform: uppercase;
  }
  .author {
    position: absolute;
    right: 52px;
    top: 1072px;
    font-family: "Gochi Hand", cursive;
    font-size: 24px;
    letter-spacing: 1.5px;
    color: var(--outline);
    text-transform: uppercase;
  }
</style>
</head>
<body>
  <main class="cover">
    <h1 class="title-main">17 GRÜNDE,</h1>
    <p class="title-sub">den Osterhasen<br>trotzdem zu mögen</p>
    <div class="divider"></div>
    <p class="tagline">DEIN HEITERER ENTSPANNUNGS-WOCHENPLANER</p>

    <svg class="illustration" viewBox="0 0 520 587" role="img" aria-label="Bereich für eine humorvolle Comic-Illustration einer grimmigen Figur mit roter Mütze">
      <defs>
        <radialGradient id="artFill" cx="0.5" cy="0.55" r="0.7">
          <stop offset="0" stop-color="var(--art-cream)"/>
          <stop offset="1" stop-color="var(--art-red)"/>
        </radialGradient>
      </defs>
      <rect x="0" y="0" width="520" height="627" rx="48" fill="url(#artFill)"/>
    </svg>

    <div class="badge">Mit schrägen Geschichten, Knobeleien und bunten Übungen.</div>

    <div class="author">Jonas Riedl</div>
  </main>
</body>
</html>
```